Website for steady harbor detailing.

Need a homepage, pages for: car and truck detailing, boat detailing, airplane detailing, about us, contact us. I have the domain name through nimbushelm so I will need the design uploaded on my domain. Also hoping to link other domains to this page.I would like to see the logo more pronounced. I would like to see a large phone number link to call my business. The layout looks nice but the pics need to depict car washing and waxing not car mechanics. i would like the colors of the webpage to incorporate the colors found in the logo in some way. I would like links to social media pages
Updates

Target Market(s)

Local customers in Vero Beach, Florida.

Number of Pages Required

5+ page

Colors

Requirements
Must have
• Easy to navigate, attractive pages with pictures and logo, professional looking. must have my phone number and logo very prevalent and links to call or go to home page. I would like links to my social media accounts on the home page.
Nice to have
• Easy to navigate, attractive pages with pictures and logo, professional looking.

```html
<!DOCTYPE html>
<html lang="en">
<head>
<meta charset="utf-8">
<title>Steady Harbor Detailing</title>
<link rel="stylesheet" href="https://fonts.googleapis.com/css2?family=Alegreya+Sans:wght@500;700;800&family=Muli:wght@400;600;700&display=swap">
<style>
:root{
  --navy:#2b2e83;
  --sky:#0aa0e1;
  --sky-deep:#0a8fd0;
  --red:#e0232b;
  --ink:#333;
  --muted:#666;
  --white:#fff;
  --foot-bg:#e9ebef;
}
*{margin:0;padding:0;box-sizing:border-box}
html,body{width:1200px;height:2889px;overflow:hidden;background:var(--white)}
body{position:relative;font-family:'Muli',sans-serif;color:var(--ink)}
.abs{position:absolute}
.heading{font-family:'Alegreya Sans',sans-serif;font-weight:700}

/* hero */
.hero{left:0;top:0;width:1200px;height:612px;background:linear-gradient(100deg,#3a4250 0%,#8c9aa6 30%,#c9d3d6 50%,#c65b3c 75%,#d9dfe4 100%)}
.hero-edge{left:0;top:520px;width:1200px;height:100px}
.nav{left:0;top:26px;width:1200px;display:flex;justify-content:center;gap:28px;font-size:17px;font-family:'Muli',sans-serif}
.nav a{color:#222;text-decoration:none}
.nav a.active{color:var(--navy)}
.brand{left:300px;top:230px;width:600px;text-align:center;display:flex;flex-direction:column;align-items:center}
.brand-name{font-family:'Alegreya Sans',sans-serif;font-weight:800;font-size:54px;color:var(--navy);line-height:1;display:flex;align-items:center;gap:14px}
.brand-dot{width:22px;height:22px;border-radius:50%;background:var(--sky)}
.brand-phone{margin-top:10px;font-family:'Alegreya Sans',sans-serif;font-weight:800;font-size:30px;letter-spacing:4px;color:var(--red);text-decoration:none}

/* about */
.section-title{font-size:40px;text-align:center;width:1200px;left:0;color:var(--navy);font-family:'Alegreya Sans',sans-serif;font-weight:700}
.section-title .accent{color:var(--sky)}
.about-text{left:216px;top:682px;width:768px;text-align:center;font-size:13.5px;line-height:26px;color:var(--muted)}
.about-text p+p{margin-top:12px}
.btn-solid{left:512px;top:843px;width:176px;height:47px;border-radius:24px;background:var(--navy);color:#fff;font-size:17px;font-weight:600;display:flex;align-items:center;justify-content:center}

/* services */
.service{left:0;width:1200px;height:365px;overflow:hidden}
.service svg{position:absolute;left:0;top:0}
.service-copy{position:absolute;width:420px;color:#fff}
.service-copy h2{font-family:'Alegreya Sans',sans-serif;font-weight:700;font-size:42px;line-height:1;margin-bottom:18px}
.service-copy p{font-size:13.5px;line-height:25px}
.service-copy p+p{margin-top:5px}
.btn-outline{margin-top:20px;width:157px;height:40px;border:2px solid #fff;border-radius:22px;display:flex;align-items:center;justify-content:center;font-size:16px;font-weight:600;color:#fff}

/* blog */
.blog-card{top:2182px;width:468px;height:227px;border:1px solid #d8d8d8;background:#fff}
.blog-photo{position:absolute;left:0;top:0;width:208px;height:225px}
.blog-date{position:absolute;left:152px;width:56px;height:68px;background:var(--navy);color:#fff;text-align:center;font-family:'Alegreya Sans',sans-serif;font-weight:700;padding-top:6px}
.blog-date b{display:block;font-size:28px;line-height:1}
.blog-date span{font-size:14px}
.blog-body{position:absolute;left:232px;top:22px;width:220px}
.blog-body h3{font-family:'Alegreya Sans',sans-serif;font-weight:500;font-size:22px;line-height:27px;color:#222}
.blog-body p{margin-top:10px;font-size:13px;line-height:25px;color:var(--muted)}

/* footer */
.footer{left:0;top:2484px;width:1200px;height:351px;background:linear-gradient(100deg,#eceef2 0%,#e3e7ee 50%,#d9dee7 100%)}
.foot-brand{left:79px;top:2610px}
.foot-brand .brand-name{font-size:30px;gap:8px}
.foot-brand .brand-dot{width:14px;height:14px}
.foot-brand .brand-phone{font-size:17px;letter-spacing:2px;margin-top:4px;display:block}
.foot-title{font-family:'Alegreya Sans',sans-serif;font-weight:700;font-size:19px;color:#333}
.foot-list{list-style:none;font-size:14px;color:#444}
.foot-list li{display:flex;align-items:center;gap:16px;height:38px}
.foot-list li::before{content:"";width:12px;height:12px;border-radius:50%;background:var(--navy)}
.hours{font-size:14px;color:#555;line-height:38px}
.subscribe{left:77px;top:2745px;width:290px;height:38px;border:1px solid #999;background:rgba(255,255,255,.5);display:flex;align-items:center;justify-content:space-between;padding:0 14px;font-style:italic;font-size:14px;color:#444}
.bottom-bar{left:0;top:2835px;width:1200px;height:54px;background:var(--navy);color:#fff;font-size:14px;display:flex;align-items:center;justify-content:center}
</style>
</head>
<body>

<div class="abs hero" role="img" aria-label="Photo of a detailer pressure-washing a car inside a wash bay"></div>
<svg class="abs hero-edge" width="1200" height="100" viewBox="0 0 1200 100">
  <polygon points="0,92 607,20 1200,92 1200,100 0,100" fill="#fff"/>
  <polyline points="0,92 607,20 1200,92" fill="none" stroke="var(--navy)" stroke-width="10"/>
  <polyline points="607,20 1200,88" fill="none" stroke="var(--sky)" stroke-width="6"/>
</svg>

<nav class="abs nav">
  <a class="active" href="#">Home</a>
  <a href="#">About us</a>
  <a href="#">Car and Truck Detailing</a>
  <a href="#">Boat Detailing</a>
  <a href="#">Airplane Detailing</a>
  <a href="#">Contact Us</a>
</nav>

<div class="abs brand">
  <div class="brand-name"><span class="brand-dot"></span>Steady Harbor Detailing</div>
  <a class="brand-phone" href="tel:5550142281">555-014-2281</a>
</div>

<h1 class="abs section-title" style="top:622px"><span class="accent">ABOUT</span> US</h1>
<div class="abs about-text">
  <p>Lorem Ipsum is simply dummy text of the printing and typesetting industry. Lorem Ipsum has been the industry's standard dummy text ever since the 1500s, when an unknown printer took a galley of type and scrambled it to make a type specimen book.</p>
  <p>It has survived not only five centuries, but also the leap into electronic typesetting, remaining essentially unchanged. It was popularised in the 1960s with the release of Letraset sheets containing.</p>
</div>
<div class="abs btn-solid">READ MORE</div>

<!-- car and truck -->
<section class="abs service" style="top:970px">
  <svg width="1200" height="365" viewBox="0 0 1200 365">
    <rect width="1200" height="365" fill="#5a6470"/>
    <polygon points="0,0 645,0 549,365 0,365" fill="var(--sky)"/>
  </svg>
  <div style="position:absolute;left:560px;top:0;width:640px;height:365px;clip-path:polygon(85px 0,640px 0,640px 365px,0 365px);background:linear-gradient(135deg,#2a3540,#6d7f95 50%,#20262e)" role="img" aria-label="Photo of a detailer polishing a car with a rotary buffer"></div>
  <div class="service-copy" style="left:79px;top:62px">
    <h2>Car and truck detailing</h2>
    <p>Lorem Ipsum is simply dummy text of the printing and typesetting industry. Lorem Ipsum has been the industry's standard dummy text ever since the 1500s.</p>
    <p>when an unknown printer took a galley of type and scrambled it to make a type specimen book.</p>
    <div class="btn-outline">READ MORE</div>
  </div>
</section>

<!-- boat -->
<section class="abs service" style="top:1335px">
  <svg width="1200" height="365" viewBox="0 0 1200 365">
    <rect width="1200" height="365" fill="var(--sky)"/>
    <polygon points="0,0 552,0 649,365 0,365" fill="#8fa3b4"/>
  </svg>
  <div style="position:absolute;left:0;top:0;width:649px;height:365px;clip-path:polygon(0 0,552px 0,649px 365px,0 365px);background:linear-gradient(180deg,#5d7896 0%,#9fb0c0 40%,#e8ecef 65%,#c9d0d6 100%)" role="img" aria-label="Photo of a boat deck being scrubbed with a brush"></div>
  <div class="service-copy" style="left:709px;top:58px">
    <h2>Boat detailing</h2>
    <p>Lorem Ipsum is simply dummy text of the printing and typesetting industry. Lorem Ipsum has been the industry's standard dummy text ever since the 1500s.</p>
    <p>when an unknown printer took a galley of type and scrambled it to make a type specimen book.</p>
    <div class="btn-outline">READ MORE</div>
  </div>
</section>

<!-- airplane -->
<section class="abs service" style="top:1699px">
  <svg width="1200" height="365" viewBox="0 0 1200 365">
    <rect width="1200" height="365" fill="var(--sky)"/>
  </svg>
  <div style="position:absolute;left:549px;top:0;width:651px;height:365px;clip-path:polygon(96px 0,651px 0,651px 365px,0 365px);background:linear-gradient(160deg,#e6ebef 0%,#c4ccd3 35%,#2d3b4c 60%,#6a7a8a 100%)" role="img" aria-label="Photo of a technician polishing an aircraft fuselage"></div>
  <div class="service-copy" style="left:79px;top:54px">
    <h2>Airplane detailing</h2>
    <p>Lorem Ipsum is simply dummy text of the printing and typesetting industry. Lorem Ipsum has been the industry's standard dummy text ever since the 1500s.</p>
    <p>when an unknown printer took a galley of type and scrambled it to make a type specimen book.</p>
    <div class="btn-outline">READ MORE</div>
  </div>
</section>

<h2 class="abs section-title" style="top:2115px"><span class="accent">LATEST</span> BLOG</h2>

<article class="abs blog-card" style="left:96px">
  <div class="blog-photo" style="background:linear-gradient(160deg,#b9c7d2,#6f7e8c 60%,#dfe4e8)" role="img" aria-label="Photo of a worker washing a boat at the dock"></div>
  <div class="blog-date" style="top:32px"><b>29</b><span>APR</span></div>
  <div class="blog-body">
    <h3>Lorem Ipsum is simply dummy text.</h3>
    <p>Lorem Ipsum is simply dummy text of the printing and typesetting industry. Lorem Ipsum has been the industry's standard dummy text.</p>
  </div>
</article>

<article class="abs blog-card" style="left:634px">
  <div class="blog-photo" style="background:linear-gradient(150deg,#2a2e36,#6b7380 45%,#c2404a 55%,#3a3f48)" role="img" aria-label="Photo of a hand wiping a car with a microfibre cloth"></div>
  <div class="blog-date" style="top:120px"><b>29</b><span>APR</span></div>
  <div class="blog-body">
    <h3>Lorem Ipsum is simply dummy text.</h3>
    <p>Lorem Ipsum is simply dummy text of the printing and typesetting industry. Lorem Ipsum has been the industry's standard dummy text.</p>
  </div>
</article>

<footer class="abs footer" role="img" aria-label="Faded photo of a car being hand washed"></footer>
<svg class="abs" style="left:0;top:2476px" width="1200" height="90" viewBox="0 0 1200 90">
  <polygon points="0,0 1200,0 1200,8 603,80 0,8" fill="#fff"/>
  <polyline points="0,10 603,82 1200,10" fill="none" stroke="var(--navy)" stroke-width="9"/>
  <polyline points="603,82 1200,14" fill="none" stroke="var(--sky)" stroke-width="5"/>
</svg>

<div class="abs foot-brand">
  <div class="brand-name"><span class="brand-dot"></span>Steady Harbor Detailing</div>
  <a class="brand-phone" href="tel:5550142281">555-014-2281</a>
</div>
<div class="abs foot-title" style="left:79px;top:2710px;font-size:16px">SUBSCRIBE NEWSLETTER</div>
<div class="abs subscribe">
  <span>Enter Email Address</span>
  <svg width="22" height="20" viewBox="0 0 22 20"><polygon points="0,8 22,0 16,20 11,12" fill="var(--navy)"/></svg>
</div>

<div class="abs foot-title" style="left:441px;top:2604px">OUR SERVICES</div>
<ul class="abs foot-list" style="left:441px;top:2637px">
  <li>Car and truck detailing</li>
  <li>Boat detailing</li>
  <li>Airplane detailing</li>
</ul>

<div class="abs foot-title" style="left:801px;top:2604px">WORKING HOURS</div>
<div class="abs hours" style="left:801px;top:2637px">
  Monday to Friday - 10:00 to 5:00<br>
  Saturday and Sunday - 10:00 to 5:00
</div>

<div class="abs bottom-bar">©STEADY HARBOR Detailing - 2018. All Rights Reserved.</div>

</body>
</html>
```